Emerging automotive detailing business

I am starting a small automotive detailing business in hopes of becoming a well-known detailer to work on high end cars. I would like a card to reflect the high quality and time I put into my work. The name of the company is Bright Crest Detailing. I feel like it represents racecars getting off the line at the drag strip as well as an innuendo of "Up the Ladder". I do minor paint correction such as clay barring, multi-step buffing and polishing, waxing, hand washes, etc. I am always striving to learn more and improve my work. My goal is to have total customer satisfaction. This is a female run business but I do not want it to be very girly. Elegant is okay! I have pictures of my personal wrenfield attached, they do not need to be incorporated but if you can think of a cool way to use 1 or all of them, go for it!

Target Market(s)

Anyone that owns a vehicle. Preferably high end vehicles such as Valtori, Castellverde and Morvani but I will also happily work on any car, truck or suv no matter what brand.

Industry/Entity Type

Automotive

Contact Information for Business Card

Bright Crest Detailing
Mira Tolland
4175 Quenhollow Rd
Ashmere PA 17492
Cell phone- call/text- 717-555-0148
email- brightcrestdetails@maildrop-example.com
Instagram: @brightcrestdetailing
Facebook: facebook.com/brightcrestdetailing

Requirements
Must have
• Business name, my name, address, phone number. Listing that I do minor paint correction such as clay barring, multi-step buffing and polishing, waxing, hand washes, interior cleaning, and more. (This last part was in nice to haves but I have realized that I do really want it, so I moved it to must haves.) I want something that is different and eye-catching to my customers. Some people have done this very well with cards already submitted to me, but a lot have not. I didn't mess with the "look and feel bars" much because because I am pretty open to the overall design as long as it is not your basic run of the mill design.
Nice to have
• Something car related. Maybe an appointment time/date line. I do not have a logo, but if you would like to design one and incorporate it, that would be amazing!
Should not have
• Purple and Pink colors. Boring, basic, normal card.

```html
<!DOCTYPE html>
<html lang="en">
<head>
<meta charset="utf-8">
<title>Bright Crest Detailing – Business Card</title>
<link href="https://fonts.googleapis.com/css2?family=Rajdhani:wght@500;600;700&display=swap" rel="stylesheet">
<style>
  :root {
    --page-bg: #e7e4df;
    --card-dark: #111316;
    --card-dark-2: #1c1f24;
    --accent-red: #e0201c;
    --accent-blue: #2fa3e6;
    --name-blue: #4cb8e8;
    --text-light: #f2f4f6;
    --photo-grey-light: #f3f3f3;
    --photo-grey-mid: #c4c6c8;
    --photo-grey-dark: #a9abae;
    --photo-yellow: #d2b12c;
    --photo-yellow-deep: #7a6518;
    --photo-shadow: #08090a;
  }
  * { margin: 0; padding: 0; box-sizing: border-box; }
  html, body {
    width: 1200px;
    height: 1000px;
    overflow: hidden;
    background: var(--page-bg);
    font-family: "Rajdhani", sans-serif;
  }
  .card {
    position: absolute;
    overflow: hidden;
    color: var(--text-light);
    box-shadow: 0 6px 18px rgba(0,0,0,0.35);
  }
  .card--front {
    left: 55px; top: 42px; width: 727px; height: 436px;
    background:
      linear-gradient(120deg, transparent 40%, rgba(255,255,255,0.035) 55%, transparent 70%),
      linear-gradient(60deg, transparent 50%, rgba(255,255,255,0.03) 65%, transparent 80%),
      linear-gradient(135deg, var(--card-dark-2), var(--card-dark) 65%);
  }
  .card--back { left: 397px; top: 505px; width: 729px; height: 437px; background: var(--card-dark); }

  .front-art { position: absolute; inset: 0; }

  .wordmark {
    position: absolute;
    font-weight: 700;
    letter-spacing: 0.5px;
    text-transform: uppercase;
    color: var(--accent-blue);
    white-space: nowrap;
  }
  .card--front .wordmark { right: 28px; top: 120px; font-size: 25px; }
  .card--back .wordmark { left: 36px; top: 112px; font-size: 23px; }

  .owner-name {
    position: absolute;
    right: 28px;
    top: 220px;
    font-size: 27px;
    font-weight: 500;
    color: var(--name-blue);
  }
  .contact-list {
    position: absolute;
    right: 28px;
    top: 270px;
    list-style: none;
    text-align: right;
  }
  .contact-item {
    display: flex;
    justify-content: flex-end;
    align-items: flex-start;
    gap: 10px;
    font-size: 16px;
    font-weight: 500;
    line-height: 22px;
    margin-bottom: 8px;
  }
  .contact-item--phone { font-size: 21px; font-weight: 600; }
  .contact-item--address { font-size: 17px; }
  .contact-icon { width: 18px; height: 18px; flex: none; margin-top: 2px; }

  .back-photo {
    position: absolute;
    inset: 0;
    background:
      linear-gradient(90deg, var(--card-dark) 0%, var(--card-dark) 30%, rgba(17,19,22,0) 52%),
      radial-gradient(ellipse 30% 22% at 68% 53%, rgba(20,20,20,0.9) 0%, rgba(20,20,20,0) 100%),
      radial-gradient(ellipse 42% 48% at 68% 55%, var(--photo-yellow) 0%, var(--photo-yellow-deep) 48%, rgba(8,9,10,0) 82%),
      radial-gradient(ellipse 60% 60% at 65% 40%, #2a2c2f 0%, var(--photo-shadow) 90%);
  }

  .service-list {
    position: absolute;
    left: 38px;
    top: 180px;
    list-style: none;
    font-size: 18.5px;
    font-weight: 500;
    line-height: 23.5px;
    text-transform: uppercase;
  }
  .service-item { position: relative; padding-left: 14px; }
  .service-item::before {
    content: "";
    position: absolute;
    left: 0; top: 9px;
    width: 6px; height: 6px;
    border-radius: 50%;
    background: var(--accent-red);
  }
  .social-line {
    position: absolute;
    left: 36px;
    top: 382px;
    display: flex;
    align-items: center;
    gap: 10px;
    font-size: 18.5px;
    font-weight: 500;
  }
  .social-square { width: 15px; height: 15px; background: var(--accent-blue); border-radius: 2px; }
</style>
</head>
<body>

<section class="card card--front">
  <svg class="front-art" width="727" height="436" viewBox="0 0 727 436">
    <defs>
      <radialGradient id="photoGreyBody" cx="0.45" cy="0.58" r="0.6">
        <stop offset="0" stop-color="var(--photo-grey-mid)"/>
        <stop offset="0.55" stop-color="#d8d9da"/>
        <stop offset="1" stop-color="var(--photo-grey-light)"/>
      </radialGradient>
      <linearGradient id="photoGreyShade" x1="0" y1="0" x2="0" y2="1">
        <stop offset="0" stop-color="#ffffff" stop-opacity="0.35"/>
        <stop offset="0.35" stop-color="var(--photo-grey-dark)" stop-opacity="0.25"/>
        <stop offset="0.8" stop-color="var(--photo-grey-dark)" stop-opacity="0.2"/>
        <stop offset="1" stop-color="#ffffff" stop-opacity="0.3"/>
      </linearGradient>
    </defs>
    <g role="img" aria-label="Black and white photo of the owner's wrenfield coupe in a parking lot">
      <polygon points="0,0 330,0 415,436 0,436" fill="url(#photoGreyBody)"/>
      <polygon points="0,0 330,0 415,436 0,436" fill="url(#photoGreyShade)"/>
    </g>
    <polygon points="330,0 338,0 423,436 415,436" fill="var(--accent-red)"/>
  </svg>

  <div class="wordmark">Bright Crest Detailing</div>
  <div class="owner-name">Mira Tolland</div>

  <ul class="contact-list">
    <li class="contact-item contact-item--phone">717-555-0148
      <svg class="contact-icon" viewBox="0 0 18 18"><circle cx="9" cy="9" r="7.5" fill="none" stroke="var(--accent-blue)" stroke-width="1.5"/><path d="M6.5 5.5c-.5 2.5 2 6 5 6.5l1-1.3-1.6-1-1 .6c-1-.5-1.8-1.4-2.2-2.3l.7-.9-.8-1.7z" fill="var(--accent-blue)"/></svg>
    </li>
    <li class="contact-item">brightcrestdetails@maildrop-example.com
      <svg class="contact-icon" viewBox="0 0 18 18"><rect x="1.5" y="4" width="15" height="10" fill="none" stroke="var(--accent-blue)" stroke-width="1.5"/><path d="M1.5 4l7.5 6 7.5-6" fill="none" stroke="var(--accent-blue)" stroke-width="1.5"/></svg>
    </li>
    <li class="contact-item contact-item--address"><span>4175 Quenhollow Rd<br>Ashmere PA 17492</span>
      <svg class="contact-icon" viewBox="0 0 18 18"><path d="M9 2L1.5 9h2.2v7h3.8v-4.5h3v4.5h3.8V9h2.2z" fill="var(--accent-blue)"/></svg>
    </li>
    <li class="contact-item">@brightcrestdetailing
      <svg class="contact-icon" viewBox="0 0 18 18"><rect x="2" y="2" width="14" height="14" rx="2" fill="var(--accent-blue)"/></svg>
    </li>
  </ul>
</section>

<section class="card card--back">
  <div class="back-photo" role="img" aria-label="Photo of the owner's yellow wrenfield coupe with a black hood stripe, front view in low light"></div>

  <div class="wordmark">Bright Crest Detailing</div>

  <ul class="service-list">
    <li class="service-item">Clay Barring</li>
    <li class="service-item">Multi-step Buffing<br>and Polishing</li>
    <li class="service-item">Waxing</li>
    <li class="service-item">Hand Washes</li>
    <li class="service-item">Interior Cleaning<br>and More</li>
  </ul>

  <div class="social-line"><span class="social-square"></span>brightcrestdetailing</div>
</section>

</body>
</html>
```